Dental Savings Plan - Raymond Castell DDS

We need a tri-fold brochure and 1 page flyer/poster for Dr. Raymond Castell' dental office located on Maui, Hawaii. We are offering a new "Dental Savings Plan" to patients.
I have included 3 photos, along with the office logo. You do not have to use all photos if you do not want to. We want this to catch the eyes of patients, easy for them to read and understand, and to show them that this is a much better option than dental insurance.
Please use same Hawaiian theme and colors on the office website https://www.brightcoveclinic.com .

Please also include the following to promote this new plan:

Dental Services Include
• Professional Dental Cleanings (2 per benefit year)
• Perio Maintenance Cleanings (3 per benefit year) covered at 80%
• Radiographs as needed (1 set of X-rays per benefit year)
• Doctor Examinations (2 per benefit year)
• Ozone Treatment
• BRISK Amalgam Removal
• Additional limited/emergency exam (1 per benefit year)
• Cosmetic consultation
• 15% discount on all other services (including cosmetic procedures)
• 10% discount on implants and implant crowns

Advantages of the Dental Savings Plan
1. No deductibles
2. No waiting periods
3. No claims to file
4. No frequency limitations or exclusions
5. No yearly maximum benefits
6. No pre-authorization requirements
7. No pre-existing conditions limitations
8. State of the art facility and technology
9. Immediate enrollment
10. Highest quality of care for you and your Ohana

Annual Fee
$399 first family member/individual (equivalent to $33 per month)
$349 second family member (equivalent to $29 per month)
$249 each additional family member (equivalent to $20 per month)

Provisions of the Dental Savings Plan
• May not be combined with insurance plans, discounts or promotions
• This Dental Savings Plan is not an insurance plan, but a payment arrangement provided by Raymond Castell DDS, and is not transferable to any other dental office or dental specialist
• Payment for services are due at the date of service
• This program is for you and is not transferable
• Benefits are provided for one year from the date the plan is purchased
• Must be paid in full when starting the plan
• No refunds will be provided for dues of the plan annual fee under any circumstances, including failure to schedule and maintain appointments
• If Pay Ladder is used to pay for the program and for services then only a 10% discount will be given
• To receive the full 15% discount on restorative treatment, you must schedule the appointment the day it is recommended. Any failed appointment results in the loss of the 15% discount.

Target Market(s)

Dental patients without dental insurance

Industry/Entity Type

Dental Clinic

Requirements
Must have
• My project must have the logo file to identify the dental office, Hawaiian theme, same colors as website, match style of website font, theme and colors, as well as, all the Dental Services, Advantages of the Dental Savings Plan, Annual Fee, and the Provisions of the Dental Savings Plan.

```html
<!DOCTYPE html>
<html lang="en">
<head>
<meta charset="utf-8">
<title>Dental Savings Plan – Raymond Castell DDS</title>
<link href="https://fonts.googleapis.com/css2?family=Open+Sans:wght@400;600;700&family=Cinzel:wght@400&display=swap" rel="stylesheet">
<style>
:root{
  --bg:#d6d7d9;
  --blue:#2b8cc4;
  --blue-deep:#1a74ad;
  --navy:#0e4c86;
  --green:#8dc63f;
  --ink:#4a4a4a;
  --white:#ffffff;
  --photo-warm:#d9b59c;
  --photo-cool:#9ec9df;
}
*{box-sizing:border-box;margin:0;padding:0}
html,body{width:879px;height:1200px;overflow:hidden;background:var(--bg);font-family:"Open Sans",Arial,sans-serif;color:var(--ink)}
.sheet{position:absolute;left:121px;width:647px;height:503px;background:var(--white);overflow:hidden}
.sheet--outside{top:67px}
.sheet--inside{top:622px}
.panel{position:absolute;top:0;height:503px;overflow:hidden}
.p1{left:0;width:211px}
.p2{left:211px;width:214px}
.p3{left:425px;width:222px}
.photo{position:absolute}
.bar{position:absolute;left:0;right:0;bottom:0;height:33px;display:flex;align-items:center;justify-content:center;font-size:9px;font-weight:700;letter-spacing:.2px}
.bar--navy{background:var(--navy);color:var(--white)}
.bar--green{background:var(--green);color:var(--white);font-size:11px}
.bar--light{background:var(--white);color:var(--green);height:23px}
.bar--light.phone{color:var(--navy);font-size:11px}
.url b{color:var(--green)}
.bar--light .url b{color:var(--green)}
.url{color:var(--white)}
.bar--light .url{color:var(--navy)}
.phone-icon{width:12px;height:12px;margin-right:6px}
/* outside left */
.doctor-tab{position:absolute;left:0;top:250px;width:137px;height:26px;background:var(--green);border-radius:0 13px 13px 0;color:var(--white);font-size:10.5px;display:flex;align-items:center;padding-left:13px}
.intro{position:absolute;left:13px;right:11px;top:285px;font-size:6.6px;line-height:1.7;text-align:justify}
.intro p{margin-bottom:9px}
/* outside middle */
.p2.contact{background:var(--blue);color:var(--white);text-align:center}
.map{position:absolute;left:45px;top:14px;width:124px;height:124px;border-radius:50%;border:4px solid var(--white);background:radial-gradient(circle at 50% 45%,#eaf2f4,#bcd8e6)}
.brand{display:flex;align-items:center;justify-content:center;gap:5px;font-size:11px;font-weight:600}
.brand-dot{width:9px;height:9px;border-radius:50%;background:var(--green)}
.contact .brand{position:absolute;left:0;right:0;top:210px;color:var(--white)}
.contact h3{font-size:10.5px;font-weight:700;margin-bottom:7px}
.contact-block{position:absolute;left:0;right:0;top:255px;font-size:7.6px;line-height:1.95}
.socials{display:flex;justify-content:center;gap:10px;margin:10px 0 12px}
.socials span{width:15px;height:15px;border-radius:50%;border:1px solid var(--white)}
.hours{font-size:6.4px;font-weight:600;line-height:1.8}
/* outside right */
.cover .brand{position:absolute;left:0;right:0;top:82px;color:var(--navy);font-size:12px}
.cover-title{position:absolute;left:0;right:0;top:398px;text-align:center;font-family:"Cinzel",Georgia,serif;color:var(--navy);font-size:23px;line-height:1.25}
/* inside */
.inside-blue{position:absolute;left:0;right:0;top:170px;bottom:23px;background:var(--blue)}
.section{position:absolute;top:232px;color:var(--white)}
.section-head{display:flex;align-items:center;gap:9px;margin-bottom:14px}
.icon-ring{width:27px;height:27px;border-radius:50%;border:1.3px solid var(--white);display:flex;align-items:center;justify-content:center;flex:none}
.section-head h3{font-size:11.5px;font-weight:700;line-height:1.35;letter-spacing:.2px}
.services{list-style:none;font-size:7px;line-height:1.85}
.services li::before{content:"• "}
.services small{font-size:5.3px}
.services .indent{padding-left:7px}
.discounts{position:absolute;left:14px;top:510px}
.discount-row{position:absolute;left:14px;top:412px;display:flex;gap:9px}
.discount{width:89px;height:52px;border:1px solid var(--green);color:var(--white);text-align:center;padding-top:8px;font-size:6.2px;line-height:1.3}
.discount strong{display:block;font-size:10px;font-weight:400}
.discount small{font-size:4.6px}
.ticks{list-style:none;font-size:6.8px;line-height:1;}
.ticks li{display:flex;align-items:center;gap:6px;height:17px}
.tick{width:7px;height:7px;flex:none}
.provisions{list-style:none;font-size:6.6px;line-height:1.2}
.provisions li{padding-left:6px;text-indent:-5px;margin-bottom:1.8px}
.provisions li::before{content:"• ";color:var(--green)}
.fee{position:absolute;left:0;top:0;width:214px;height:218px;background:linear-gradient(180deg,#2f86c0 0%,#3a9fd0 55%,#2a8ac0 100%)}
.fee-title{position:absolute;left:33px;top:36px;width:136px;height:25px;border:1px solid var(--green);color:var(--white);font-size:15px;display:flex;align-items:center;justify-content:center;font-weight:600}
.fee-list{position:absolute;left:13px;top:76px;list-style:none;color:var(--white);font-size:8.2px;line-height:1.45}
.fee-list li{display:flex;gap:5px;margin-bottom:9px}
.fee-list b{color:var(--green);font-weight:400}
</style>
</head>
<body>

<!-- OUTSIDE -->
<section class="sheet sheet--outside">
  <div class="panel p1">
    <div class="photo" role="img" aria-label="Portrait of Dr. Raymond Castell in a white coat in the clinic" style="left:0;top:0;width:211px;height:237px;background:linear-gradient(135deg,#c9dbe6,#d5b8a4 55%,#8fb6c9)"></div>
    <svg style="position:absolute;left:0;top:0" width="211" height="60" viewBox="0 0 211 60"><path d="M0 0H211V28C150 10 70 18 0 50Z" fill="var(--blue)"/><path d="M0 50C70 18 150 10 211 28V32C150 15 70 22 0 55Z" fill="var(--green)"/></svg>
    <div class="doctor-tab">Dr. Raymond Castell</div>
    <div class="intro">
      <p>Welcome to Bright Cove Clinic – Cosmetic and Advanced Dentistry in South Maui!</p>
      <p>We pride ourselves on consistently delivering top-quality dentistry to the wonderful people of Maui. We love our patients and our patients love us! We focus on one patient at a time, making sure you are heard and valued.</p>
      <p>As leaders in biological dentistry we focus on prevention, providing safer, less toxic and more individualized dentistry. As leaders in beautiful reconstruction dentistry we are committed to delivering beautiful, genuine life changing smiles.</p>
    </div>
    <div class="bar bar--navy">RESERVE AN APPOINTMENT</div>
  </div>

  <div class="panel p2 contact">
    <div class="map" role="img" aria-label="Street map of the Kihei area marking the clinic location"></div>
    <div class="brand"><span class="brand-dot"></span>Raymond Castell DDS</div>
    <div class="contact-block">
      <h3>CONTACT US</h3>
      808-555-0172<br>
      4410 Lani Kai Rd # 112, Kihei, HI 96753<br>
      hello@brightcoveclinic.com
      <div class="socials"><span></span><span></span><span></span><span></span></div>
      <h3>OUR HOURS</h3>
      <div class="hours">Monday Closed<br>Tuesday 8:30 am - 5:00 pm<br>Wednesday 8:30 am - 5:00 pm<br>Thursday 8:30 am - 5:00 pm<br>Friday 8:30 am-5:00 pm<br>Saturday -Closed</div>
    </div>
    <div class="bar bar--green"><svg class="phone-icon" viewBox="0 0 12 12"><circle cx="6" cy="6" r="5.3" fill="none" stroke="#fff" stroke-width="1"/><path d="M4 3.3l1 1.4-.6.7c.4.9 1.1 1.6 2 2l.7-.6 1.4 1-.6 1c-2.3-.3-4.2-2.2-4.5-4.5z" fill="#fff"/></svg>808-555-0172</div>
  </div>

  <div class="panel p3 cover">
    <svg style="position:absolute;left:0;top:0" width="222" height="130" viewBox="0 0 222 130"><path d="M0 0H222V80C150 130 60 118 0 104Z" fill="var(--white)"/></svg>
    <div class="photo" role="img" aria-label="Smiling young woman with long brown hair" style="left:0;top:100px;width:222px;height:260px;background:linear-gradient(160deg,#a9c7a0,#d8b39a 50%,#6d8f6c)"></div>
    <svg style="position:absolute;left:0;top:70px" width="222" height="60" viewBox="0 0 222 60"><path d="M0 0H222V10C150 55 60 50 0 38Z" fill="var(--white)"/><path d="M0 38C60 50 150 55 222 10V18C150 62 60 56 0 44Z" fill="var(--navy)"/><path d="M0 44C60 56 150 62 222 18V22C150 66 60 60 0 48Z" fill="var(--green)"/></svg>
    <svg style="position:absolute;left:0;top:340px" width="222" height="40" viewBox="0 0 222 40"><path d="M0 10C70 30 150 28 222 8V40H0Z" fill="var(--white)"/><path d="M0 4C70 24 150 22 222 2V8C150 28 70 30 0 10Z" fill="var(--green)"/></svg>
    <div class="brand"><span class="brand-dot"></span>Raymond Castell DDS</div>
    <div class="cover-title">DENTAL<br>SAVINGS PLAN</div>
    <div class="bar bar--navy"><span class="url">www.<b>brightcoveclinic</b>.com</span></div>
  </div>
</section>

<!-- INSIDE -->
<section class="sheet sheet--inside">
  <div class="inside-blue"></div>

  <div class="panel p1">
    <div class="photo" role="img" aria-label="Close-up of a patient's open smile during a dental check-up" style="left:0;top:0;width:211px;height:200px;background:linear-gradient(120deg,#e8c9b4,#f3efee 60%,#cfd8de)"></div>
    <div class="section" style="left:13px;width:190px">
      <div class="section-head"><span class="icon-ring"><svg width="14" height="14" viewBox="0 0 14 14"><path d="M3 2c1.5-.8 2.7 0 4 0s2.5-.8 4 0c1.5 1 .8 4-.2 5.5L10 12c-.3.8-1 .6-1.2-.2L8 9c-.3-.8-1.7-.8-2 0l-.8 2.8c-.2.8-.9 1-1.2.2L3.2 7.5C2.2 6 1.5 3 3 2z" fill="none" stroke="#fff" stroke-width=".9"/></svg></span><h3>DENTAL SERVICES<br>INCLUDE</h3></div>
      <ul class="services">
        <li>Professional Dental Cleanings <small>(2 per benefit year)</small></li>
        <li>Perio Maintenance Cleanings <small>(3 per benefit year)</small></li>
        <li class="indent" style="list-style:none">covered at 80%</li>
        <li>Radiographs as needed <small>(1 set of X-rays per benefit year)</small></li>
        <li>Doctor Examinations <small>(2 per benefit year)</small></li>
        <li>Ozone Treatment</li>
        <li>BRISK Amalgam Removal</li>
        <li>Additional limited/emergency exam <small>(1 per benefit year)</small></li>
        <li>Cosmetic consultation</li>
      </ul>
    </div>
    <div class="discount-row">
      <div class="discount"><strong>15% discount</strong>on all other services<br><small>(including cosmetic procedures)</small></div>
      <div class="discount"><strong>10% discount</strong>on implants and<br>implant crowns</div>
    </div>
    <div class="bar bar--light">RESERVE AN APPOINTMENT</div>
  </div>

  <div class="panel p2">
    <div class="fee" role="img" aria-label="Tropical beach with palm trees and ocean"></div>
    <div class="fee-title">ANNUAL FEE</div>
    <ul class="fee-list">
      <li><svg class="tick" viewBox="0 0 8 8"><circle cx="4" cy="4" r="3.5" fill="none" stroke="#8dc63f" stroke-width=".8"/><path d="M2.3 4l1.2 1.2 2.3-2.4" fill="none" stroke="#8dc63f" stroke-width=".8"/></svg><span><b>$399</b> first family member/individual<br>(equivalent to $33 per month)</span></li>
      <li><svg class="tick" viewBox="0 0 8 8"><circle cx="4" cy="4" r="3.5" fill="none" stroke="#8dc63f" stroke-width=".8"/><path d="M2.3 4l1.2 1.2 2.3-2.4" fill="none" stroke="#8dc63f" stroke-width=".8"/></svg><span><b>$349</b> second family member<br>(equivalent to $29 per month)</span></li>
      <li><svg class="tick" viewBox="0 0 8 8"><circle cx="4" cy="4" r="3.5" fill="none" stroke="#8dc63f" stroke-width=".8"/><path d="M2.3 4l1.2 1.2 2.3-2.4" fill="none" stroke="#8dc63f" stroke-width=".8"/></svg><span><b>$249</b> each additional family member<br>(equivalent to $20 per month)</span></li>
    </ul>
    <div class="section" style="left:12px;width:196px">
      <div class="section-head"><span class="icon-ring"><svg width="14" height="14" viewBox="0 0 14 14"><circle cx="7" cy="7" r="5.5" fill="#fff"/><path d="M7 7V1.5A5.5 5.5 0 0 1 12.5 7Z" fill="var(--blue)"/></svg></span><h3>ADVANTAGES OF THE<br>DENTAL SAVINGS PLAN</h3></div>
      <ul class="ticks">
        <li><svg class="tick" viewBox="0 0 8 8"><circle cx="4" cy="4" r="3.5" fill="none" stroke="#8dc63f" stroke-width=".8"/><path d="M2.3 4l1.2 1.2 2.3-2.4" fill="none" stroke="#8dc63f" stroke-width=".8"/></svg>No deductibles</li>
        <li><svg class="tick" viewBox="0 0 8 8"><circle cx="4" cy="4" r="3.5" fill="none" stroke="#8dc63f" stroke-width=".8"/><path d="M2.3 4l1.2 1.2 2.3-2.4" fill="none" stroke="#8dc63f" stroke-width=".8"/></svg>No waiting periods</li>
        <li><svg class="tick" viewBox="0 0 8 8"><circle cx="4" cy="4" r="3.5" fill="none" stroke="#8dc63f" stroke-width=".8"/><path d="M2.3 4l1.2 1.2 2.3-2.4" fill="none" stroke="#8dc63f" stroke-width=".8"/></svg>No claims to file</li>
        <li><svg class="tick" viewBox="0 0 8 8"><circle cx="4" cy="4" r="3.5" fill="none" stroke="#8dc63f" stroke-width=".8"/><path d="M2.3 4l1.2 1.2 2.3-2.4" fill="none" stroke="#8dc63f" stroke-width=".8"/></svg>No frequency limitations or exclusions</li>
        <li><svg class="tick" viewBox="0 0 8 8"><circle cx="4" cy="4" r="3.5" fill="none" stroke="#8dc63f" stroke-width=".8"/><path d="M2.3 4l1.2 1.2 2.3-2.4" fill="none" stroke="#8dc63f" stroke-width=".8"/></svg>No yearly maximum benefits</li>
        <li><svg class="tick" viewBox="0 0 8 8"><circle cx="4" cy="4" r="3.5" fill="none" stroke="#8dc63f" stroke-width=".8"/><path d="M2.3 4l1.2 1.2 2.3-2.4" fill="none" stroke="#8dc63f" stroke-width=".8"/></svg>No pre-authorization requirements</li>
        <li><svg class="tick" viewBox="0 0 8 8"><circle cx="4" cy="4" r="3.5" fill="none" stroke="#8dc63f" stroke-width=".8"/><path d="M2.3 4l1.2 1.2 2.3-2.4" fill="none" stroke="#8dc63f" stroke-width=".8"/></svg>No pre-existing conditions limitations</li>
        <li><svg class="tick" viewBox="0 0 8 8"><circle cx="4" cy="4" r="3.5" fill="none" stroke="#8dc63f" stroke-width=".8"/><path d="M2.3 4l1.2 1.2 2.3-2.4" fill="none" stroke="#8dc63f" stroke-width=".8"/></svg>State of the art facility and technology</li>
        <li><svg class="tick" viewBox="0 0 8 8"><circle cx="4" cy="4" r="3.5" fill="none" stroke="#8dc63f" stroke-width=".8"/><path d="M2.3 4l1.2 1.2 2.3-2.4" fill="none" stroke="#8dc63f" stroke-width=".8"/></svg>Immediate enrollment</li>
        <li><svg class="tick" viewBox="0 0 8 8"><circle cx="4" cy="4" r="3.5" fill="none" stroke="#8dc63f" stroke-width=".8"/><path d="M2.3 4l1.2 1.2 2.3-2.4" fill="none" stroke="#8dc63f" stroke-width=".8"/></svg>Highest quality of care for you and your Ohana</li>
      </ul>
    </div>
    <div class="bar bar--light phone"><svg class="phone-icon" viewBox="0 0 12 12"><circle cx="6" cy="6" r="5.3" fill="none" stroke="#8dc63f" stroke-width="1"/><path d="M4 3.3l1 1.4-.6.7c.4.9 1.1 1.6 2 2l.7-.6 1.4 1-.6 1c-2.3-.3-4.2-2.2-4.5-4.5z" fill="#8dc63f"/></svg>808-555-0172</div>
  </div>

  <div class="panel p3">
    <div class="photo" role="img" aria-label="Happy family of four outdoors on a sunny day" style="left:0;top:0;width:222px;height:220px;background:linear-gradient(170deg,#cfe3ee,#d8b9a1 55%,#eef1f2)"></div>
    <div class="section" style="left:14px;width:202px">
      <div class="section-head"><span class="icon-ring" style="font-size:13px;font-weight:600">%</span><h3>PROVISIONS OF THE<br>DENTAL SAVINGS PLAN</h3></div>
      <ul class="provisions">
        <li>May not be combined with insurance plans, discounts or promotions</li>
        <li>This Dental Savings Plan is not an insurance plan, but a payment arrangement provided by Raymond Castell DDS, and is not transferable to any other dental office or dental specialist</li>
        <li>Payment for services are due at the date of service</li>
        <li>This program is for you and is not transferable</li>
        <li>Benefits are provided for one year from the date the plan is purchased</li>
        <li>Must be paid in full when starting the plan</li>
        <li>No refunds will be provided for dues of the plan annual fee under any circumstances, including failure to schedule and maintain appointments</li>
        <li>If Pay Ladder is used to pay for the program and for services then only a 10% discount will be given</li>
        <li>To receive the full 15% discount on restorative treatment, you must schedule the appointment the day it is recommended. Any failed appointment results in the loss of the 15% discount.</li>
      </ul>
    </div>
    <div class="bar bar--light"><span class="url">www.<b>brightcoveclinic</b>.com</span></div>
  </div>

  <svg style="position:absolute;left:0;top:160px" width="647" height="70" viewBox="0 0 647 70"><path d="M0 30C100 8 180 10 211 18C300 40 380 50 425 48C520 40 600 20 647 0V12C600 32 520 52 425 58C380 60 300 50 211 28C180 20 100 18 0 40Z" fill="var(--green)"/><path d="M0 40C100 18 180 20 211 28C300 50 380 60 425 58C520 52 600 32 647 12V70H0Z" fill="var(--blue)"/></svg>
</section>

</body>
</html>
```